Business Card Design of an established Waste Management, Plastic Recycling and Renewable Energy Comp

We are looking for business card design for plastic card with holograms (Very similar to credit card). I will provide our logo (Quenbys). So the name on the business card will be our logo )Quenbys) + Environmental next to it, so it will read Quenbys Environmental. The font for Environmental does not to be the same as the font of the logo. The holograms will be used to display ISO14001 Certified (In normal credit card, normally on the holograms, they show nova or kelo). I will post the design requirements from the card printing company very shortly to make sure they can use the design for the plastic card.

Target Market(s)

Companies, Government Organizations, Corporations.

Industry/Entity Type

Business

Contact Information for Business Card

Motto (Under the logo): Let's Do It Right
Name: Leopold Maresca; Position: Business Manager; Address: Pelmore Landfill & Recycling Facility, Tressingham Rd, Brenfield Vale, WA 6187; Ph: +61 8 5210 4738; Mob: +61 455 903 172; E: Leo@quenbysenvironmental-mail.com

Requirements
Must have
• Business Names: Quenbys Logo + Environmental word after the logo.
• Motto (Under the logo): Let's Do It Right
• All the Business Card Details above.
• Hologram Logo on the lower right corner which says: ISO 14001 Certified.
• Please remember the design will be printed on plastic card Not paper. The plastic crad is the same as credit card. Hope this helps. Thank You

```html
<!DOCTYPE html>
<html lang="en">
<head>
<meta charset="utf-8">
<title>Quenbys Environmental – Business Card</title>
<link rel="stylesheet" href="https://fonts.googleapis.com/css2?family=Open+Sans:wght@400;600;700&display=swap">
<style>
  :root {
    --stage: #050608;
    --brand-blue: #0098dc;
    --brand-blue-deep: #1f63a8;
    --ink-grey: #57585a;
    --paper: #ffffff;
    --badge-line: #1a1a1a;
  }
  * { box-sizing: border-box; margin: 0; padding: 0; }
  html, body {
    width: 1200px; height: 900px; overflow: hidden;
    background: var(--stage);
    font-family: "Open Sans", Arial, sans-serif;
  }
  .stage { position: relative; width: 1200px; height: 900px; }

  .card {
    position: absolute; top: 271px;
    width: 457px; height: 281px;
    border-radius: 14px; overflow: hidden;
  }
  .card--front { left: 137px; background: var(--brand-blue); }
  .card--back  { left: 626px; background: var(--brand-blue); }

  .front-header {
    position: absolute; left: 0; top: 0; width: 100%; height: 126px;
    background: var(--paper);
  }
  .front-stripe {
    position: absolute; left: 0; top: 126px; width: 100%; height: 7px;
    background: var(--brand-blue-deep);
  }
  .front-stripe-gap {
    position: absolute; left: 0; top: 133px; width: 100%; height: 4px;
    background: var(--paper);
  }

  .wordmark { position: absolute; display: flex; align-items: center; gap: 10px; }
  .wordmark__dot { width: 58px; height: 58px; border-radius: 50%; flex: none; }
  .wordmark__text { display: flex; flex-direction: column; font-weight: 600; }
  .wordmark__name { font-size: 50px; line-height: 50px; letter-spacing: -0.5px; }
  .wordmark__sub { font-size: 14px; line-height: 16px; letter-spacing: 4.2px; text-transform: uppercase; margin-top: 4px; }

  .card--front .wordmark { left: 23px; top: 32px; }
  .card--front .wordmark__dot { background: var(--brand-blue); }
  .card--front .wordmark__text { color: var(--ink-grey); }

  .card--back .wordmark { left: 92px; top: 104px; }
  .card--back .wordmark__dot { background: var(--paper); }
  .card--back .wordmark__text { color: var(--paper); }

  .cert-badge {
    position: absolute; left: 366px; top: 40px;
    width: 71px; height: 56px;
    border: 2px solid var(--badge-line); border-radius: 6px;
    display: flex; align-items: center; justify-content: center;
  }
  .cert-badge__ring {
    width: 44px; height: 44px; border-radius: 50%;
    border: 2px solid var(--badge-line);
  }

  .person { position: absolute; left: 23px; top: 146px; color: var(--paper); }
  .person__name { font-size: 16.5px; font-weight: 600; line-height: 22px; }
  .person__role { font-size: 12px; line-height: 16px; }

  .contact-list {
    position: absolute; right: 19px; top: 164px;
    list-style: none; color: var(--paper);
    font-size: 12px; line-height: 19px; text-align: right;
  }
  .contact-list li { display: flex; justify-content: flex-end; align-items: center; gap: 6px; }
  .contact-list svg { width: 10px; height: 10px; fill: var(--paper); flex: none; }

  .address {
    position: absolute; left: 23px; top: 227px;
    color: var(--paper); font-size: 12px; line-height: 16px; font-style: normal;
  }
</style>
</head>
<body>
<main class="stage">

  <section class="card card--front" aria-label="Business card front">
    <div class="front-header"></div>
    <div class="front-stripe"></div>
    <div class="front-stripe-gap"></div>

    <div class="wordmark">
      <span class="wordmark__dot"></span>
      <div class="wordmark__text">
        <span class="wordmark__name">Quenbys</span>
        <span class="wordmark__sub">Environmental</span>
      </div>
    </div>

    <div class="cert-badge" aria-label="Certification hologram">
      <span class="cert-badge__ring"></span>
    </div>

    <div class="person">
      <p class="person__name">Leopold Maresca</p>
      <p class="person__role">Business Manager</p>
    </div>

    <ul class="contact-list">
      <li>+61 8 5210 4738
        <svg viewBox="0 0 10 10" aria-hidden="true"><path d="M2 0.5 L3.6 0.5 L4.3 2.8 L3.2 3.7 Q4.2 5.8 6.3 6.8 L7.2 5.7 L9.5 6.4 L9.5 8 Q9.5 9.5 8 9.5 Q0.5 9 0.5 2 Q0.5 0.5 2 0.5Z"/></svg>
      </li>
      <li>+61 455 903 172
        <svg viewBox="0 0 10 10" aria-hidden="true"><path d="M2.5 0 H7.5 Q8.3 0 8.3 0.8 V9.2 Q8.3 10 7.5 10 H2.5 Q1.7 10 1.7 9.2 V0.8 Q1.7 0 2.5 0Z M2.7 1.2 V8 H7.3 V1.2Z"/></svg>
      </li>
      <li>Leo@quenbysenvironmental-mail.com
        <svg viewBox="0 0 10 10" aria-hidden="true"><path d="M0.5 2 H9.5 V8 H0.5Z M1 2.5 L5 5.6 L9 2.5" stroke="#0098dc" stroke-width="0.8"/></svg>
      </li>
    </ul>

    <address class="address">
      Pelmore Landfill &amp; Recycling Facility<br>
      Tressingham Rd, Brenfield Vale, WA 6187
    </address>
  </section>

  <section class="card card--back" aria-label="Business card back">
    <div class="wordmark">
      <span class="wordmark__dot"></span>
      <div class="wordmark__text">
        <span class="wordmark__name">Quenbys</span>
        <span class="wordmark__sub">Environmental</span>
      </div>
    </div>
  </section>

</main>
</body>
</html>
```